SOLVE Study flyer

I need help designing a flyer for a research study that will include brain imaging in adolescents. The info is in the attached document. The study is called the Sequoia Outlook Lantern Valley Echo (SOLVE) study. Ideally this would be returned as a document that I can edit in the future as we will have several new recruitment phases (different age groups, etc. I also would love to have a logo designed as part of this project, but I recognize that might be a separate design request.

```html
<!DOCTYPE html>
<html lang="en">
<head>
<meta charset="utf-8">
<title>SOLVE Study Recruitment Flyer</title>
<link rel="stylesheet" href="https://fonts.googleapis.com/css2?family=Poppins:wght@400;500;600;700&display=swap">
<style>
  :root {
    --navy: #141c4f;
    --plum: #3a1838;
    --crimson: #c10000;
    --deep-red: #8d0616;
    --night: #0b1a4c;
    --charcoal: #1d1d1f;
    --gold: #f7b519;
    --gold-dim: #b8731e;
    --white: #ffffff;
    --photo-grey: #9aa2a8;
    --photo-coral: #e2674a;
  }
  * { box-sizing: border-box; margin: 0; padding: 0; }
  html, body { width: 927px; height: 1200px; overflow: hidden; }
  body { font-family: "Poppins", sans-serif; color: var(--white); }

  .flyer {
    position: relative;
    width: 927px;
    height: 1200px;
    overflow: hidden;
    background: linear-gradient(180deg,
      var(--navy) 0%,
      var(--plum) 17%,
      var(--deep-red) 33%,
      var(--crimson) 50%,
      var(--deep-red) 68%,
      var(--plum) 83%,
      var(--night) 100%);
  }
  .decor { position: absolute; left: 0; top: 0; width: 927px; height: 1200px; }

  .title {
    position: absolute; left: 0; right: 0; top: 28px;
    text-align: center; font-size: 58px; font-weight: 600; letter-spacing: 0.5px; line-height: 1.2;
  }
  .subtitle {
    position: absolute; left: 0; right: 0; top: 102px;
    text-align: center; font-size: 21px; font-weight: 600; line-height: 1.3;
  }
  .headline {
    position: absolute; left: 0; right: 0; top: 238px;
    text-align: center; font-size: 33px; font-weight: 600; line-height: 44px;
  }

  .brand {
    position: absolute; left: 36px; top: 370px;
    display: flex; align-items: center; gap: 16px;
  }
  .brand-mark { width: 70px; height: 70px; background: var(--gold); }
  .brand-name { font-size: 36px; font-weight: 500; line-height: 1.1; color: var(--white); }

  .intro {
    position: absolute; left: 440px; top: 364px; width: 444px;
    font-size: 17.5px; line-height: 27px; text-align: justify; letter-spacing: 0.2px;
  }
  .intro strong { font-weight: 700; }

  .section-heading {
    position: absolute; left: 36px; font-size: 27px; font-weight: 600; line-height: 1.3;
  }
  .section-heading.involves { top: 512px; }
  .section-heading.eligible { top: 780px; }

  .bullets {
    position: absolute; left: 36px; width: 484px; list-style: none;
    font-size: 17.5px; line-height: 24.6px;
  }
  .bullets li { position: relative; padding-left: 28px; text-align: justify; }
  .bullets li::before {
    content: ""; position: absolute; left: 1px; top: 8px;
    width: 8px; height: 8px; border-radius: 50%; background: var(--white);
  }
  .bullets.involves { top: 566px; }
  .bullets.involves li + li { margin-top: 20px; }
  .bullets.eligible { top: 834px; }
  .bullets.eligible li + li { margin-top: 15px; }

  .photo {
    position: absolute; left: 584px; top: 560px; width: 308px; height: 308px; border-radius: 50%;
    border: 3px solid var(--gold);
    background: radial-gradient(circle at 62% 42%, var(--photo-coral) 0%, #c8745f 22%, var(--photo-grey) 50%, #cfd3d6 100%);
    box-shadow: 0 6px 18px rgba(0,0,0,0.35);
  }

  .contact-heading { position: absolute; left: 36px; top: 1014px; font-size: 25px; font-weight: 600; line-height: 1.3; }
  .contact-sub { position: absolute; left: 36px; top: 1056px; font-size: 16.5px; font-weight: 600; line-height: 1.3; }
  .contact-email { position: absolute; left: 34px; top: 1094px; font-size: 32px; font-weight: 600; line-height: 1.3; color: var(--gold); }

  .compensation {
    position: absolute; left: 623px; top: 1008px;
    font-size: 35px; font-weight: 600; line-height: 44px;
  }
  .compensation .amount { color: var(--gold); display: block; }
</style>
</head>
<body>
  <main class="flyer">
    <svg class="decor" viewBox="0 0 927 1200" aria-hidden="true">
      <circle cx="758" cy="983" r="122" fill="none" stroke="var(--gold-dim)" stroke-width="1"/>
      <circle cx="758" cy="1196" r="122" fill="none" stroke="var(--gold-dim)" stroke-width="1"/>
      <circle cx="822" cy="1122" r="276" fill="none" stroke="var(--gold)" stroke-width="1.4"/>
    </svg>
    <svg class="decor" viewBox="0 0 927 1200" role="img" aria-label="Dark band with a pattern of hand-drawn speech and thought bubbles">
      <path d="M0 0 H927 V48 Q480 330 0 22 Z" fill="var(--charcoal)"/>
    </svg>

    <h1 class="title">SOLVE Study</h1>
    <p class="subtitle">(Sequoia Outlook Lantern Valley Echo)</p>
    <h2 class="headline">Are you the parent of a child 10-17?<br>Do they worry or overthink negative emotions?</h2>

    <div class="brand">
      <span class="brand-mark"></span>
      <span class="brand-name">Northvale<br>University</span>
    </div>

    <p class="intro">Northvale University researchers are seeking <strong>Girls Age 10-17</strong> for a about brain activity in emotions and decision-making and how they relate to puberty, anxiety and depression.</p>

    <h3 class="section-heading involves">Study Partcipation involves:</h3>
    <ul class="bullets involves">
      <li>One one-hour interview (online or in-person) where your child will discuss their thoughts.</li>
      <li>Online questionnaires (parent and child)</li>
      <li>One two-hour visit where your child will complete an MRI scan, answer questions about their puberty stage, and have a small hair sample taken to study puberty hormones</li>
    </ul>

    <div class="photo" role="img" aria-label="Photo of a stressed teenage girl in a coral shirt holding her head at a desk with a laptop and a cup"></div>

    <h3 class="section-heading eligible">Your child may be eligible if they:</h3>
    <ul class="bullets eligible">
      <li>Are age 10-17</li>
      <li>Tend to worry or overthink negative thoughts</li>
      <li>Have not been diagnosed with psychosis, learning problems, or autism</li>
    </ul>

    <h3 class="contact-heading">Interested in participating?</h3>
    <p class="contact-sub">Want more information? Please contact us!</p>
    <p class="contact-email">solvestudy@northvale.edu</p>

    <p class="compensation">Partcipation<br>Compensation<span class="amount">Up to $140</span></p>
  </main>
</body>
</html>
```